Dental specialist needs a sharp looking letterhead

I am looking for a letterhead to be used to send letters and communication between myself (a dental specialist) and other dentists.
My office is a state of the art dental specialty office.
I need to letterhead to also state:
Bertram L. Oswick DDS
2748 Tollard Avenue, Suite K
West Tollard, NY 14391
(716)392-5061
fax: (716)392-5087
oswickroot.com (**this email address may change)

i included my logo designs.
thank you

Target Market(s)

dentists

Industry/Entity Type

Communication

Requirements
Must have
• the included logo, whether the vertical or horizontal versions

```html
<!DOCTYPE html>
<html lang="en">
<head>
<meta charset="utf-8">
<title>Cedarline Endodontics Letterhead</title>
<link href="https://fonts.googleapis.com/css2?family=Bitter:wght@400;500&display=swap" rel="stylesheet">
<style>
  :root {
    --paper: #ffffff;
    --ink: #1d1d1d;
    --ink-soft: #333333;
    --rule: #3a3a3a;
    --brand-blue: #43a4dc;
    --brand-green: #8cc63f;
    --backdrop: #ffffff;
  }
  * { margin: 0; padding: 0; box-sizing: border-box; }
  html, body {
    width: 932px;
    height: 1200px;
    overflow: hidden;
    background: var(--backdrop);
  }
  .letterhead {
    position: relative;
    width: 932px;
    height: 1200px;
    background: var(--paper);
    font-family: "Bitter", Georgia, serif;
    color: var(--ink);
  }
  .brand {
    position: absolute;
    left: 35px;
    top: 33px;
    display: flex;
    align-items: center;
    height: 96px;
  }
  .brand-dot {
    width: 72px;
    height: 72px;
    border-radius: 50%;
    background: var(--brand-blue);
    margin-right: 14px;
  }
  .brand-rule {
    width: 1px;
    height: 96px;
    background: var(--rule);
    margin-right: 8px;
  }
  .brand-name {
    font-weight: 500;
    color: var(--ink);
    line-height: 1;
  }
  .brand-name .main {
    display: block;
    font-size: 38px;
    letter-spacing: -0.5px;
  }
  .brand-name .sub {
    display: block;
    font-size: 15px;
    letter-spacing: 1.6px;
    margin-top: 4px;
    padding-left: 27px;
  }
  .contact {
    position: absolute;
    left: 654px;
    top: 37px;
    height: 104px;
    border-left: 1px solid var(--rule);
    padding-left: 19px;
    font-size: 16.5px;
    color: var(--ink-soft);
  }
  .contact .address { line-height: 20px; margin-top: -1px; }
  .contact .lines { margin-top: 6px; }
  .contact .line {
    display: flex;
    align-items: center;
    height: 21.5px;
  }
  .contact svg {
    width: 15px;
    height: 13px;
    margin-right: 4px;
    fill: var(--ink-soft);
  }
  .footer {
    position: absolute;
    left: 0;
    bottom: 0;
    width: 932px;
    height: 120px;
  }
  .footer svg { display: block; }
  .doctor-name {
    position: absolute;
    left: 0;
    right: 0;
    bottom: 22px;
    text-align: center;
    color: #ffffff;
    font-size: 20px;
    letter-spacing: 0.3px;
  }
</style>
</head>
<body>
  <main class="letterhead">
    <header>
      <div class="brand">
        <div class="brand-dot"></div>
        <div class="brand-rule"></div>
        <div class="brand-name">
          <span class="main">CEDARLINE</span>
          <span class="sub">Endodontics P.C.</span>
        </div>
      </div>

      <address class="contact">
        <div class="address">2748 Tollard Avenue, Suite K<br>West Tollard, NY 14391</div>
        <div class="lines">
          <div class="line">
            <svg viewBox="0 0 16 16" aria-hidden="true"><path d="M3.6 1.2l2.3 3.1-1.3 1.6c.9 2 2.5 3.6 4.5 4.5l1.6-1.3 3.1 2.3-1.2 2.4C7.2 14 2 8.8 1.2 3.4z"/></svg>
            <span>716-392-5061</span>
          </div>
          <div class="line">
            <svg viewBox="0 0 16 14" aria-hidden="true"><path d="M4 1h7l1 3H3zM1 5h14v6h-2v2h-2v-2H5v2H3v-2H1z"/></svg>
            <span>716-392-5087</span>
          </div>
          <div class="line">
            <svg viewBox="0 0 16 12" aria-hidden="true"><path d="M1 1h14v1.2L8 7 1 2.2z M1 3.8l7 4.8 7-4.8V11H1z"/></svg>
            <span>oswickroot@tollardmail.com</span>
          </div>
        </div>
      </address>
    </header>

    <footer class="footer">
      <svg width="932" height="120" viewBox="0 0 932 120" aria-hidden="true">
        <path d="M0 92 Q466 -32 932 92 Q466 -22 0 92 Z" fill="var(--brand-green)"/>
        <path d="M0 92 Q466 -14 932 92 L932 120 L0 120 Z" fill="var(--brand-blue)"/>
      </svg>
      <p class="doctor-name">Bertram L. Oswick, DDS</p>
    </footer>
  </main>
</body>
</html>
```